Business card

We need a business card design for our company based in Auckland , New Zealand called 'Ridge + Studio Ltd'. We provide architectural services. We would like to see designs that use the max. three colours (such as white, black, grey) The final design should communicate financial safety and growth."
Also I will provide our company logo. I would like to the logo to be embeded onto our business card.

Target Market(s)

new residential house, alteration & addition & light commericila design & drafting service

Industry/Entity Type

Architecture

Contact Information for Business Card

Company name: ridge + studio Ltd.
Name: Mark Delford
Job title: architectural designer & Design LBP
email address: mark@rplusd.co.nz
mobile number: 02 5163 2290
web site: www.rplusd.co.nz

Requirements
Must have
• My project must have..
• - embeded logo (attached company logo)
• I don't have a bigger version for our company logo, but I have one old one, so you can remove the word from it)
• - insert the attached small BKTW logo & LBP logo
• - creative, simple and clear business card.
• - Max. three colours
Nice to have
• - Here are the samples I would like to share with you: http://www.plimvora.com/blog/minimalistic-business-card-designs/
• I would like to have my business card like one of the creation.
Should not have
• TBA

```html
<!DOCTYPE html>
<html lang="en">
<head>
<meta charset="utf-8">
<title>Ridge + Studio Ltd — Business Card</title>
<link rel="stylesheet" href="https://fonts.googleapis.com/css2?family=Montserrat:wght@400;500;700&display=swap">
<style>
  :root {
    --ink: #0b0b0b;
    --paper: #ffffff;
    --grey: #6e6e6e;
    --stage: #d9d9d9;
  }
  * { box-sizing: border-box; margin: 0; padding: 0; }
  html, body { width: 1200px; height: 900px; overflow: hidden; }
  body {
    background: var(--stage);
    font-family: 'Montserrat', sans-serif;
    display: flex; align-items: center; justify-content: center; gap: 60px;
  }
  .card {
    position: relative; width: 520px; height: 300px;
    border-radius: 22px; overflow: hidden;
    box-shadow: 0 10px 30px rgba(0,0,0,.25);
  }

  /* back side */
  .card--back { background: var(--ink); color: var(--paper); }
  .brand {
    position: absolute; left: 0; right: 0; top: 92px;
    display: flex; justify-content: center; align-items: center; gap: 12px;
  }
  .brand-square { width: 14px; height: 14px; background: var(--paper); }
  .brand-name { font-size: 24px; font-weight: 700; letter-spacing: .2px; }
  .back-web {
    position: absolute; left: 0; right: 0; top: 134px;
    text-align: center; font-size: 13px; font-weight: 500;
  }
  .badges {
    position: absolute; left: 0; right: 0; top: 172px;
    display: flex; justify-content: center; align-items: flex-start; gap: 22px;
  }
  .member { display: flex; flex-direction: column; align-items: center; gap: 6px; }
  .badge-member { width: 52px; height: 40px; background: var(--grey); border-radius: 3px; }
  .member-label {
    font-size: 10px; font-weight: 700; line-height: 1.15; color: var(--grey); text-align: center;
  }
  .badge-lbp {
    width: 56px; height: 56px; border-radius: 50%;
    background: var(--paper); border: 4px solid var(--grey);
  }

  /* front side */
  .card--front { background: var(--paper); }
  .front-band { position: absolute; left: 0; top: 0; width: 100%; height: 178px; background: var(--ink); }
  .front-company {
    position: absolute; left: 30px; top: 30px; color: var(--paper);
    font-size: 16px; font-weight: 700;
  }
  .person { position: absolute; left: 30px; top: 96px; color: var(--paper); }
  .person-name { font-size: 26px; font-weight: 700; letter-spacing: .5px; }
  .person-role { font-size: 13px; font-weight: 400; line-height: 1.3; margin-top: 2px; }
  .contacts {
    position: absolute; left: 30px; top: 196px; list-style: none;
    color: var(--ink); font-size: 13px; font-weight: 500;
  }
  .contacts li { display: flex; align-items: center; gap: 10px; height: 24px; }
  .contacts svg { width: 13px; height: 13px; flex: none; }
</style>
</head>
<body>
  <section class="card card--back" aria-label="Card back">
    <div class="brand">
      <span class="brand-square" aria-hidden="true"></span>
      <p class="brand-name">Ridge + Studio Ltd</p>
    </div>
    <p class="back-web">www.rplusd.co.nz</p>
    <div class="badges">
      <div class="member">
        <div class="badge-member" role="img" aria-label="Professional membership badge"></div>
        <p class="member-label">Professional<br>Member</p>
      </div>
      <div class="badge-lbp" role="img" aria-label="Licensed building practitioner badge"></div>
    </div>
  </section>

  <section class="card card--front" aria-label="Card front">
    <div class="front-band"></div>
    <p class="front-company">Ridge + Studio Ltd</p>
    <div class="person">
      <h1 class="person-name">MARK DELFORD</h1>
      <p class="person-role">Architectural designer<br>&amp; Design LBP</p>
    </div>
    <ul class="contacts">
      <li><svg viewBox="0 0 16 16" aria-hidden="true"><path d="M3 1l3 3-2 2c1 2 3 4 5 5l2-2 3 3-2 3C7 15 1 9 1 3z" fill="var(--ink)"/></svg>02 5163 2290</li>
      <li><svg viewBox="0 0 16 16" aria-hidden="true"><rect x="1" y="3" width="14" height="10" fill="none" stroke="var(--ink)" stroke-width="1.6"/><path d="M1 3l7 6 7-6" fill="none" stroke="var(--ink)" stroke-width="1.6"/></svg>mark@rplusd.co.nz</li>
      <li><svg viewBox="0 0 16 16" aria-hidden="true"><circle cx="8" cy="8" r="7" fill="none" stroke="var(--ink)" stroke-width="1.5"/><path d="M1 8h14M8 1c-3 4-3 10 0 14M8 1c3 4 3 10 0 14" fill="none" stroke="var(--ink)" stroke-width="1.2"/></svg>www.rplusd.co.nz</li>
    </ul>
  </section>
</body>
</html>
```